Orrisdale Gift Co Flyer

We need a 'marketing' flyer for our online luxury hamper business which has recently launched.
In order to market ourselves at upcoming events, we need a beautiful and stylish double sided A5 card to hand out to guests and to include in event bags.
I would like to include our logo and one styled image of some products on the A5 card.

It will need to include our tag line - Text tbc and contact details which will be website; www.orrisdalegiftco.com.au and social media icons; facebook, instagram and pinterest

Thank you

Target Market(s)

20 - 40 market

Industry/Entity Type

Business

```html
<!DOCTYPE html>
<html lang="en">
<head>
<meta charset="utf-8">
<title>Orrisdale Gift Co – Flyer Back Variations</title>
<link rel="stylesheet" href="https://fonts.googleapis.com/css2?family=Raleway:wght@400;500&display=swap">
<style>
  :root {
    --backdrop: #ecebe8;
    --card: #ffffff;
    --card-edge: #2a2a2a;
    --ink-light: #b9b9b9;
    --ink-mid: #4a4a4a;
    --ink-dark: #111111;
    --icon-light: #b0b0b0;
    --icon-mid: #6a6a6a;
    --icon-dark: #111111;
  }
  * { box-sizing: border-box; margin: 0; padding: 0; }
  html, body { width: 1200px; height: 900px; overflow: hidden; }
  body {
    background: var(--backdrop);
    font-family: 'Raleway', sans-serif;
  }
  .flyer-row {
    position: absolute;
    top: 195px;
    left: 22px;
    display: flex;
    gap: 8px;
  }
  .flyer-back {
    width: 380px;
    height: 510px;
    background: var(--card);
    border: 1px solid var(--card-edge);
    position: relative;
    color: var(--ink);
  }
  .flyer-back--light { --ink: var(--ink-light); --icon: var(--icon-light); }
  .flyer-back--mid   { --ink: var(--ink-mid);   --icon: var(--icon-mid); }
  .flyer-back--dark  { --ink: var(--ink-dark);  --icon: var(--icon-dark); }

  .tagline {
    position: absolute;
    top: 132px;
    left: 28px;
    right: 28px;
    text-align: center;
    font-size: 12.5px;
    line-height: 15.5px;
    letter-spacing: 0.9px;
    font-weight: 400;
  }
  .product-shots {
    position: absolute;
    top: 206px;
    left: 14px;
    right: 14px;
    display: flex;
    justify-content: space-between;
  }
  .product-shot {
    width: 169px;
    height: 122px;
  }
  .product-shot--stationery {
    background: linear-gradient(135deg, #5f7d86 0%, #c9b98a 35%, #e8e2d2 55%, #d56a4f 75%, #8fa89c 100%);
  }
  .product-shot--grooming {
    background: linear-gradient(135deg, #d9d1c1 0%, #8c7a62 40%, #2c2824 65%, #e4ddd0 100%);
  }
  .contact {
    position: absolute;
    top: 357px;
    left: 0;
    right: 0;
    text-align: center;
    font-size: 12.5px;
    line-height: 20.5px;
    letter-spacing: 0.8px;
  }
  .follow-label {
    position: absolute;
    top: 424px;
    left: 0;
    right: 0;
    text-align: center;
    font-size: 10.5px;
    letter-spacing: 1.4px;
    text-transform: uppercase;
  }
  .social-row {
    position: absolute;
    top: 451px;
    left: 0;
    right: 0;
    display: flex;
    justify-content: center;
    gap: 14px;
  }
  .social-row svg { display: block; }
  .social-mark { fill: var(--icon); }
</style>
</head>
<body>
  <main class="flyer-row">
    <section class="flyer-back flyer-back--light" aria-label="Orrisdale Gift Co flyer back, light grey text">
      <p class="tagline">We're dedicated to curating products that are off the beaten track and making it easy for you to give them to the people you love.</p>
      <div class="product-shots">
        <div class="product-shot product-shot--stationery" role="img" aria-label="Styled flat lay of books, candles, tea and succulents"></div>
        <div class="product-shot product-shot--grooming" role="img" aria-label="Styled flat lay of a magazine, amber bottle, candle and playing cards"></div>
      </div>
      <address class="contact" style="font-style:normal">
        www.orrisdalegiftco.com.au<br>
        sales@orrisdalegiftco.com.au<br>
        1300 482 517
      </address>
      <p class="follow-label">Follow us</p>
      <div class="social-row" aria-label="Social media links">
        <svg width="18" height="18" role="img" aria-label="Social link"><rect class="social-mark" width="18" height="18" rx="2"/></svg>
        <svg width="18" height="18" role="img" aria-label="Social link"><circle class="social-mark" cx="9" cy="9" r="9"/></svg>
        <svg width="18" height="18" role="img" aria-label="Social link"><rect class="social-mark" width="18" height="18" rx="4"/></svg>
      </div>
    </section>

    <section class="flyer-back flyer-back--mid" aria-label="Orrisdale Gift Co flyer back, mid grey text">
      <p class="tagline">We're dedicated to curating products that are off the beaten track and making it easy for you to give them to the people you love.</p>
      <div class="product-shots">
        <div class="product-shot product-shot--stationery" role="img" aria-label="Styled flat lay of books, candles, tea and succulents"></div>
        <div class="product-shot product-shot--grooming" role="img" aria-label="Styled flat lay of a magazine, amber bottle, candle and playing cards"></div>
      </div>
      <address class="contact" style="font-style:normal">
        www.orrisdalegiftco.com.au<br>
        sales@orrisdalegiftco.com.au<br>
        1300 482 517
      </address>
      <p class="follow-label">Follow us</p>
      <div class="social-row" aria-label="Social media links">
        <svg width="18" height="18" role="img" aria-label="Social link"><rect class="social-mark" width="18" height="18" rx="2"/></svg>
        <svg width="18" height="18" role="img" aria-label="Social link"><circle class="social-mark" cx="9" cy="9" r="9"/></svg>
        <svg width="18" height="18" role="img" aria-label="Social link"><rect class="social-mark" width="18" height="18" rx="4"/></svg>
      </div>
    </section>

    <section class="flyer-back flyer-back--dark" aria-label="Orrisdale Gift Co flyer back, black text">
      <p class="tagline">We're dedicated to curating products that are off the beaten track and making it easy for you to give them to the people you love.</p>
      <div class="product-shots">
        <div class="product-shot product-shot--stationery" role="img" aria-label="Styled flat lay of books, candles, tea and succulents"></div>
        <div class="product-shot product-shot--grooming" role="img" aria-label="Styled flat lay of a magazine, amber bottle, candle and playing cards"></div>
      </div>
      <address class="contact" style="font-style:normal">
        www.orrisdalegiftco.com.au<br>
        sales@orrisdalegiftco.com.au<br>
        1300 482 517
      </address>
      <p class="follow-label">Follow us</p>
      <div class="social-row" aria-label="Social media links">
        <svg width="18" height="18" role="img" aria-label="Social link"><rect class="social-mark" width="18" height="18" rx="2"/></svg>
        <svg width="18" height="18" role="img" aria-label="Social link"><circle class="social-mark" cx="9" cy="9" r="9"/></svg>
        <svg width="18" height="18" role="img" aria-label="Social link"><rect class="social-mark" width="18" height="18" rx="4"/></svg>
      </div>
    </section>
  </main>
</body>
</html>
```